Dental office stationary (letterhead, envelopes), business cards, presentation folders

Nothing too dental outside of the logo. I will need all stationary, presentation folders, business cards. Would prefer to stay in the colors of the logo

Gordon Patel, DDS
Bright Haven Dental Implant Center
555-318-2790
info@brighthavendental.example
4817 NW Maple Crest Rd Unit B
Harbor Glen, ST 00000

Also need appointment date and time
And cancellation policy
I want it to say “kindly ask for
A 48hr cancellation policy to avoid incurring a cancellation fee”

Industry/Entity Type

Dental

Colors
0054AA
0677BA
7BADD7
CADEEF
E8F1F8

Requirements
Must have
• Name of your office, name of doctor, address, phone number
Should not have
• Too much tooth/dental. Only the tooth in logo

```html
<!DOCTYPE html>
<html lang="en">
<head>
<meta charset="utf-8">
<title>Bright Haven Dental Implant Center – Business Card</title>
<link rel="stylesheet" href="https://fonts.googleapis.com/css2?family=Arimo:wght@400&family=Tinos:wght@700&display=swap">
<style>
  :root {
    --page-bg: #3c3c3c;
    --card-white: #ffffff;
    --card-dark: #2d2d2d;
    --blue-deep: #0a6cbf;
    --blue-light: #1a9ad8;
    --brand-blue: #0677BA;
    --brand-teal: #1bb39a;
    --text-light: #ffffff;
  }
  * { margin: 0; padding: 0; box-sizing: border-box; }
  html, body { width: 1200px; height: 803px; overflow: hidden; }
  body {
    background: var(--page-bg);
    position: relative;
    font-family: "Arimo", Arial, sans-serif;
  }
  .card {
    position: absolute;
    top: 253px;
    width: 520px;
    height: 297px;
    border-radius: 18px;
    overflow: hidden;
  }
  .card--front { left: 50px; background: var(--card-white); display: flex; }
  .card--back {
    left: 630px;
    background: var(--card-dark);
    border: 1.5px solid #cfcfcf;
    display: flex;
    align-items: center;
    justify-content: center;
  }
  .front__brand {
    width: 45%;
    display: flex;
    align-items: center;
    justify-content: center;
    padding: 0 12px;
  }
  .front__divider { width: 5px; background: var(--brand-teal); }
  .front__info {
    flex: 1;
    background: radial-gradient(circle at 60% 30%, var(--blue-light), var(--blue-deep) 75%);
    color: var(--text-light);
    padding: 44px 20px 0 30px;
  }
  .info__name {
    font-family: "Tinos", "Times New Roman", serif;
    font-weight: 700;
    font-size: 20px;
    letter-spacing: 0.5px;
    text-transform: uppercase;
  }
  .info__title { font-size: 11px; margin-top: 2px; }
  .info__address { font-size: 11.5px; line-height: 1.35; margin-top: 20px; }
  .info__contacts { list-style: none; margin-top: 18px; font-size: 11.5px; line-height: 1.5; }
  .info__contacts li { display: flex; align-items: center; gap: 7px; white-space: nowrap; }
  .info__contacts svg { width: 10px; height: 10px; flex: none; }
  .brand-name {
    font-family: "Tinos", "Times New Roman", serif;
    font-weight: 700;
    color: var(--brand-blue);
    text-align: center;
    display: flex;
    align-items: center;
    gap: 10px;
  }
  .brand-name__mark { border-radius: 50%; background: var(--brand-teal); flex: none; }
  .brand-name--small { font-size: 17px; line-height: 1.2; }
  .brand-name--small .brand-name__mark { width: 14px; height: 14px; }
  .brand-name--large { font-size: 34px; line-height: 1.15; color: var(--brand-teal); }
  .brand-name--large .brand-name__mark { width: 24px; height: 24px; background: var(--brand-blue); }
</style>
</head>
<body>
  <section class="card card--front" aria-label="Business card front">
    <div class="front__brand">
      <div class="brand-name brand-name--small">
        <span class="brand-name__mark"></span>
        <span>Bright Haven<br>Dental Implant Center</span>
      </div>
    </div>
    <div class="front__divider"></div>
    <div class="front__info">
      <h1 class="info__name">Gordon Patel</h1>
      <p class="info__title">DDS</p>
      <p class="info__address">4817 NW Maple Crest Rd Unit B<br>Harbor Glen, ST 00000</p>
      <ul class="info__contacts">
        <li>
          <svg viewBox="0 0 10 10" aria-hidden="true"><path d="M2 0.5 L3.6 2.6 L2.7 3.6 Q3.8 6 6.4 7.3 L7.4 6.4 L9.5 8 L8.3 9.5 Q2 8.5 0.5 1.7 Z" fill="#fff"/></svg>
          555-318-2790
        </li>
        <li>
          <svg viewBox="0 0 10 10" aria-hidden="true"><rect x="0.5" y="2" width="9" height="6.5" fill="#fff"/><path d="M0.5 2 L5 5.6 L9.5 2" fill="none" stroke="#0a6cbf" stroke-width="0.9"/></svg>
          info@brighthavendental.example
        </li>
        <li>
          <svg viewBox="0 0 10 10" aria-hidden="true"><circle cx="5" cy="5" r="4.5" fill="#fff"/><path d="M0.5 5 H9.5 M5 0.5 Q2.5 5 5 9.5 M5 0.5 Q7.5 5 5 9.5" fill="none" stroke="#0a6cbf" stroke-width="0.7"/></svg>
          www.brighthavendental.example
        </li>
      </ul>
    </div>
  </section>

  <section class="card card--back" aria-label="Business card back">
    <div class="brand-name brand-name--large">
      <span class="brand-name__mark"></span>
      <span>Bright Haven<br>Dental Implant Center</span>
    </div>
  </section>
</body>
</html>
```